Stylish new business card needed!

Hello everyone! I am in need of a new business card design for an alarm company here in Hurricane WV. I have all fonts, color codes and logos provided for you use! We are a young company and like the style of a clean sleek looking business card. Would like it double sided, one side holding the logo and the other with your design!
Target Market(s)
The people that are looking for the newest tech for home automation and security
Industry/Entity Type
Alarm services; Home automation
Contact Information for Business Card
Name of person; position (Sales; Installer); Phone Number (555.418.7260); Employee cell Number; Website (www.GuardedByVelk.example); Employee Email; Double sided
Look and feel
Each slider illustrates characteristics of the customer's brand and the style your logo design should communicate.

```html
<!DOCTYPE html>
<html lang="en">
<head>
<meta charset="utf-8">
<title>Velk Business Card</title>
<link rel="stylesheet" href="https://fonts.googleapis.com/css2?family=Archivo+Black&family=Lato:wght@400;700;900&display=swap">
<style>
  :root {
    --bg: #e9e6e2;
    --card: #1d1d1d;
    --card-shade: #232323;
    --ring: #2c2c2c;
    --orange: #f68f4a;
    --white: #ffffff;
    --grey: #b9b9b9;
  }
  * { box-sizing: border-box; margin: 0; padding: 0; }
  html, body { width: 1200px; height: 977px; overflow: hidden; background: var(--bg); }
  .canvas { position: relative; width: 1200px; height: 977px; }
  .card {
    position: absolute; left: 300px; width: 600px; height: 343px;
    background: var(--card); border-radius: 22px; overflow: hidden;
    box-shadow: 0 8px 24px rgba(0,0,0,.25);
  }
  .card--front { top: 105px; }
  .card--back { top: 529px; }

  /* front */
  .front-lockup {
    position: absolute; inset: 0; display: flex; flex-direction: column;
    align-items: center; justify-content: center;
  }
  .front-eyebrow {
    font-family: "Archivo Black", sans-serif; color: var(--orange);
    font-size: 30px; letter-spacing: 1px;
  }
  .front-name {
    display: flex; align-items: center; gap: 18px;
    font-family: "Lato", sans-serif; font-weight: 900; color: var(--orange);
    font-size: 104px; line-height: 1; letter-spacing: 6px; margin: 6px 0 10px;
  }
  .front-mark { width: 30px; height: 30px; border-radius: 50%; background: var(--orange); }
  .front-tagline {
    font-family: "Archivo Black", sans-serif; color: var(--orange);
    font-size: 15px; letter-spacing: 1px;
  }

  /* back */
  .back-art { position: absolute; inset: 0; }
  .back-brand {
    position: absolute; left: 22px; top: 0; height: 343px; width: 170px;
    display: flex; align-items: center; justify-content: center;
    font-family: "Lato", sans-serif; font-weight: 700; color: var(--white);
    font-size: 52px; letter-spacing: 4px;
  }
  .contact {
    position: absolute; right: 34px; top: 84px; text-align: right;
    font-family: "Lato", sans-serif;
  }
  .contact-name { color: var(--orange); font-weight: 900; font-size: 30px; letter-spacing: .5px; }
  .contact-role { color: var(--grey); font-size: 17px; margin-bottom: 12px; }
  .contact-line {
    display: flex; justify-content: flex-end; align-items: center; gap: 8px;
    color: var(--white); font-size: 16px; line-height: 25px;
  }
  .contact-line--small { font-size: 14px; }
  .contact-icon { width: 13px; height: 13px; flex: none; }
</style>
</head>
<body>
<div class="canvas">

  <section class="card card--front">
    <div class="front-lockup">
      <div class="front-eyebrow">GUARDED BY</div>
      <div class="front-name"><span>VELK</span><span class="front-mark"></span></div>
      <div class="front-tagline">AUTOMATION AND SECURITY SERVICES</div>
    </div>
  </section>

  <section class="card card--back">
    <svg class="back-art" width="600" height="343" viewBox="0 0 600 343">
      <circle cx="-80" cy="200" r="330" fill="var(--ring)"/>
      <circle cx="-120" cy="200" r="300" fill="var(--orange)"/>
      <circle cx="495" cy="170" r="240" fill="var(--card-shade)" stroke="#333" stroke-width="1"/>
      <circle cx="510" cy="180" r="180" fill="#202020"/>
    </svg>
    <div class="back-brand">VELK</div>
    <div class="contact">
      <div class="contact-name">DANIEL REYES</div>
      <div class="contact-role">Sales &amp; Installer</div>
      <div class="contact-line">555.418.7260
        <svg class="contact-icon" viewBox="0 0 16 16"><path fill="var(--orange)" d="M3 1l3 3-2 2c1 2 3 4 5 5l2-2 3 3-2 3C7 15 1 9 1 3z"/></svg>
      </div>
      <div class="contact-line">555.418.7390
        <svg class="contact-icon" viewBox="0 0 16 16"><rect x="4" y="1" width="8" height="14" rx="1.5" fill="none" stroke="var(--orange)" stroke-width="2"/></svg>
      </div>
      <div class="contact-line contact-line--small">daniel@guardedbyvelk.example
        <svg class="contact-icon" viewBox="0 0 16 16"><rect x="1" y="3" width="14" height="10" fill="var(--orange)"/><path d="M1 3l7 6 7-6" fill="none" stroke="var(--card)" stroke-width="1.5"/></svg>
      </div>
      <div class="contact-line contact-line--small">GuardedByVelk.example
        <svg class="contact-icon" viewBox="0 0 16 16"><circle cx="8" cy="8" r="7" fill="var(--orange)"/><path d="M1 8h14M8 1c-3 4-3 10 0 14M8 1c3 4 3 10 0 14" fill="none" stroke="var(--card)" stroke-width="1"/></svg>
      </div>
    </div>
  </section>

</div>
</body>
</html>
```